New tech executive consulting company needs professionally branded document templates

We are a new business selling fractional board advisory and go-to-market consulting services into the Technology space. Tessaly Brink are experts in providing high-quality executive-level leaders on a part-time basis to tech companies in need of their expertise. We work closely with clients to understand their business needs, challenges, and goals, and provides customised solutions to help them succeed. Due to our audience we need the design to have a high quality, executive look and feel.

Our first website is live and can be found at tessalybrink.example. We also already have a logo which I've uploaded. Our brand is clean and uses orange to give it colour and an identity that stands out.

We need some document master templates created so we can create our own presentations (Google Slides & Powerpoint), PDF documents, and Word templates, and ideally also a LinkedIn banner.

```html
<!DOCTYPE html>
<html lang="en">
<head>
<meta charset="utf-8">
<title>Tessaly Brink – Presentation Template</title>
<link rel="stylesheet" href="https://fonts.googleapis.com/css2?family=Montserrat:wght@500;700;800&family=Inter:wght@400;500&display=swap">
<style>
  :root{
    --canvas:#5f5f5f;
    --paper:#f1f1f2;
    --paper-light:#fafafa;
    --navy:#2b3442;
    --navy-deep:#1f2733;
    --orange:#ef8143;
    --white:#ffffff;
    --ink:#1e2530;
    --body:#39404a;
  }
  *{box-sizing:border-box;margin:0;padding:0}
  html,body{width:1200px;height:4127px;overflow:hidden;background:var(--canvas)}
  body{position:relative;font-family:"Inter",sans-serif}
  .slide{position:absolute;left:40px;width:1120px;height:630px;overflow:hidden;background:linear-gradient(135deg,var(--paper-light),var(--paper))}
  .slide svg.backdrop{position:absolute;inset:0;width:1120px;height:630px}
  .heading{font-family:"Montserrat",sans-serif;font-weight:800;color:var(--ink);text-transform:uppercase;position:absolute}
  .wordmark{position:absolute;font-family:"Montserrat",sans-serif;font-weight:800;color:var(--orange);text-transform:uppercase;letter-spacing:1px;line-height:1}
  .wordmark.small{right:28px;top:28px;font-size:19px;text-align:right;line-height:1.15}
  .copy{position:absolute;font-size:14px;line-height:1.55;color:var(--body)}
  .copy p+p{margin-top:18px}

  /* cover */
  .cover{top:37px}
  .cover .wordmark{left:110px;top:185px;font-size:104px}
  .cover .wordmark span{display:block}
  .cover .wordmark span+span{margin-left:500px;margin-top:4px}
  .cover .tagline{position:absolute;left:115px;top:325px;font-family:"Montserrat",sans-serif;font-weight:700;font-size:26px;line-height:47px;color:var(--white);text-transform:uppercase}

  /* agenda */
  .agenda{top:718px}
  .agenda .heading{left:630px;top:108px;font-size:36px}
  .agenda-item{position:absolute;display:flex;align-items:center;gap:22px;font-family:"Montserrat",sans-serif;font-weight:800;font-size:26px;color:var(--ink);text-transform:uppercase}
  .agenda-num{width:58px;height:58px;border-radius:50%;display:flex;align-items:center;justify-content:center;color:var(--white);font-size:21px;border:3px solid var(--white);box-shadow:0 2px 6px rgba(0,0,0,.15)}
  .num-orange{background:var(--orange)}
  .num-navy{background:var(--navy)}

  /* about */
  .about{top:1397px}
  .about .heading{left:93px;top:150px;font-size:37px;line-height:50px;color:var(--white)}
  .about .copy{left:93px;top:320px;width:560px;font-size:13.5px;color:#e6e9ee}

  /* founder */
  .founder{top:2078px}
  .founder .heading{left:490px;top:160px;font-size:38px}
  .founder .copy{left:490px;top:222px;width:560px;font-size:14px;line-height:28px}

  /* contact call */
  .call{top:2759px}
  .call .heading{left:0;width:1120px;top:72px;font-size:38px;line-height:51px;text-align:center}

  /* closing */
  .closing{top:3436px}
  .closing .wordmark{left:340px;top:150px;font-size:56px;color:var(--white)}
  .closing .wordmark span{display:block}
  .closing .wordmark span+span{margin-left:230px;margin-top:4px}
  .closing .heading{left:355px;top:322px;font-size:37px;color:var(--white)}
  .contact-row{position:absolute;left:355px;display:flex;align-items:center;gap:12px;color:var(--white);font-size:17px;line-height:1.35}
  .contact-icon{width:40px;height:40px;border-radius:50%;background:var(--orange);display:flex;align-items:center;justify-content:center;flex:none}
</style>
</head>
<body>

<!-- Cover -->
<section class="slide cover">
  <svg class="backdrop" viewBox="0 0 1120 630">
    <defs>
      <linearGradient id="coverPhoto" x1="0" y1="0" x2="1" y2="1">
        <stop offset="0" stop-color="#4a5a70"/><stop offset="1" stop-color="#1e2734"/>
      </linearGradient>
    </defs>
    <polygon points="0,0 940,0 560,630 0,630" fill="url(#coverPhoto)" role="img" aria-label="Photo of executives meeting around a boardroom table"/>
    <polygon points="0,170 100,0 108,0 0,185" fill="#ffffff"/>
    <polygon points="932,128 962,128 612,490 582,490" fill="var(--orange)"/>
  </svg>
  <div class="wordmark"><span>Tessaly</span><span>Brink</span></div>
  <div class="tagline">Experts in providing<br>executive leadership on</div>
</section>

<!-- Agenda -->
<section class="slide agenda">
  <svg class="backdrop" viewBox="0 0 1120 630">
    <defs>
      <linearGradient id="agendaPhoto" x1="0" y1="0" x2="1" y2="1">
        <stop offset="0" stop-color="#c9cfd3"/><stop offset=".6" stop-color="#8a8278"/><stop offset="1" stop-color="#e4e2de"/>
      </linearGradient>
    </defs>
    <polygon points="0,0 620,0 300,630 0,630" fill="url(#agendaPhoto)" role="img" aria-label="Photo of three colleagues discussing work around a laptop"/>
    <polygon points="620,0 655,0 335,630 300,630" fill="var(--orange)"/>
  </svg>
  <div class="heading">Agenda</div>
  <div class="agenda-item" style="left:465px;top:240px"><span class="agenda-num num-orange">01</span>About us</div>
  <div class="agenda-item" style="left:418px;top:342px"><span class="agenda-num num-navy">02</span>Marcus Hale</div>
  <div class="agenda-item" style="left:372px;top:446px"><span class="agenda-num num-orange">03</span>Let us help you</div>
</section>

<!-- About -->
<section class="slide about">
  <svg class="backdrop" viewBox="0 0 1120 630">
    <defs>
      <linearGradient id="aboutPhoto" x1="0" y1="0" x2="1" y2="1">
        <stop offset="0" stop-color="#6d655d"/><stop offset=".5" stop-color="#b3a595"/><stop offset="1" stop-color="#d9dde2"/>
      </linearGradient>
    </defs>
    <rect x="43" y="112" width="1077" height="473" rx="4" fill="var(--navy)"/>
    <polygon points="865,112 1120,112 1120,585 570,585" fill="url(#aboutPhoto)" role="img" aria-label="Photo of smiling colleagues reviewing documents at a desk"/>
    <polygon points="910,0 965,0 545,630 490,630" fill="var(--orange)"/>
  </svg>
  <div class="wordmark small">Tessaly<br>Brink</div>
  <div class="heading">About<br>The smart way to scale<br>your business</div>
  <div class="copy">
    <p>Tessaly Brink are experts in providing high-quality executive-level leaders on a part-time basis to tech companies in need of their expertise. We work closely with clients to understand their business needs, challenges, and goals, and provides customised solutions to help them succeed.</p>
    <p>Our strategic insights, leadership, and collaborative approach make us a valuable partner for companies looking to drive growth and innovation. We are passionate about helping companies achieve their goals and are committed to providing the highest level of service to our clients.</p>
  </div>
</section>

<!-- Founder -->
<section class="slide founder">
  <svg class="backdrop" viewBox="0 0 1120 630">
    <defs>
      <linearGradient id="founderPhoto" x1="0" y1="0" x2="0" y2="1">
        <stop offset="0" stop-color="#b49a6c"/><stop offset=".5" stop-color="#8a6d56"/><stop offset="1" stop-color="#2f4f8a"/>
      </linearGradient>
    </defs>
    <polygon points="440,0 500,0 80,630 20,630" fill="var(--orange)"/>
    <rect x="58" y="78" width="382" height="480" fill="url(#founderPhoto)" role="img" aria-label="Portrait photo of the founder in a blue blazer"/>
  </svg>
  <div class="wordmark small">Tessaly<br>Brink</div>
  <div class="heading">Marcus Hale</div>
  <div class="copy">
    <p>Marcus Hale is a highly accomplished business leader with extensive experience in executive-level leadership and strategy. As the founder of Tessaly Brink, Marcus brings his years of experience in the technology industry to help companies achieve their goals.</p>
    <p>Throughout his career, Marcus has held executive positions in companies ranging from startups to large corporations. He has a deep understanding of the tech industry and has helped companies at all stages of maturity drive significant growth and innovation.</p>
  </div>
</section>

<!-- Call to action -->
<section class="slide call">
  <svg class="backdrop" viewBox="0 0 1120 630">
    <defs>
      <linearGradient id="callPhoto" x1="0" y1="0" x2="1" y2="1">
        <stop offset="0" stop-color="#3d4a58"/><stop offset=".5" stop-color="#8c8a84"/><stop offset="1" stop-color="#d8dadc"/>
      </linearGradient>
    </defs>
    <polygon points="0,245 1120,500 1120,630 0,630" fill="var(--orange)"/>
    <rect x="170" y="254" width="780" height="340" rx="18" fill="url(#callPhoto)" stroke="#ffffff" stroke-width="3" role="img" aria-label="Photo of two colleagues working together at a computer"/>
  </svg>
  <div class="wordmark small">Tessaly<br>Brink</div>
  <div class="heading">Let us help you take your business to<br>the next level. Contact us for a free<br>consultation.</div>
</section>

<!-- Closing -->
<section class="slide closing">
  <svg class="backdrop" viewBox="0 0 1120 630">
    <defs>
      <radialGradient id="closingPhoto" cx=".5" cy=".4" r=".7">
        <stop offset="0" stop-color="#5a4a36"/><stop offset=".6" stop-color="#2a2a28"/><stop offset="1" stop-color="#1a1c1e"/>
      </radialGradient>
    </defs>
    <rect width="1120" height="630" fill="url(#closingPhoto)" role="img" aria-label="Blurred photo of an office with a hanging light bulb"/>
    <polygon points="0,0 170,0 0,290" fill="var(--paper)"/>
    <polygon points="170,0 240,0 60,290 20,290" fill="var(--navy)"/>
    <polygon points="1120,0 1120,630 760,630" fill="var(--paper)"/>
    <polygon points="1040,280 1090,280 880,630 770,630" fill="var(--orange)"/>
  </svg>
  <div class="wordmark"><span>Tessaly</span><span>Brink</span></div>
  <div class="heading">Thank you</div>
  <div class="contact-row" style="top:378px">
    <span class="contact-icon"><svg width="18" height="18" viewBox="0 0 24 24"><path d="M12 2a7 7 0 0 0-7 7c0 5 7 13 7 13s7-8 7-13a7 7 0 0 0-7-7zm0 9.5A2.5 2.5 0 1 1 12 6.5a2.5 2.5 0 0 1 0 5z" fill="#fff"/></svg></span>
    <span>12b Tessaly Brink Lorem ipsum<br>dolor sit amet, consectetur</span>
  </div>
  <div class="contact-row" style="top:452px">
    <span class="contact-icon"><svg width="18" height="18" viewBox="0 0 24 24"><path d="M6.6 10.8a15 15 0 0 0 6.6 6.6l2.2-2.2a1 1 0 0 1 1-.25 11.4 11.4 0 0 0 3.6.57 1 1 0 0 1 1 1V20a1 1 0 0 1-1 1A17 17 0 0 1 3 4a1 1 0 0 1 1-1h3.5a1 1 0 0 1 1 1c0 1.25.2 2.45.57 3.57a1 1 0 0 1-.25 1z" fill="#fff"/></svg></span>
    <span>+1 555 010 0199</span>
  </div>
  <div class="contact-row" style="top:514px">
    <span class="contact-icon"><svg width="18" height="18" viewBox="0 0 24 24"><path d="M3 5h18v14H3z" fill="#fff"/><path d="M3 5l9 7 9-7" fill="none" stroke="#ef8143" stroke-width="2"/></svg></span>
    <span>info@tessalybrink.example</span>
  </div>
</section>

</body>
</html>
```